Gardener needs an exciting new flyer design.

I'm a passionate gardener that requires a custom flyer design for a owner operator gardening business. Design will be for a DL flyer. I'm based on the Sunshine coast in Queensland Australia. My target audience is the residential market on the Sunshine coast. Business name is Marlowe Grove. My services are, lawn mowing, weeding, Eco Friendly fertilizing, green waste removal, Mulching, tree and shrub pruning, Full garden makeovers, hedging, pressure cleaning, privacy screening, Timber deck rejuvenation, Planting, Turf preparation and installation, and much more. Free no obligation quotes, reliable and friendly service, great rates. 12 years experience. Web www.marlowegrove.com.au - Phone 0481527306 - Email tom@marlowegrove.com.au I would like the design to portray a friendly and professional approach.

Target Market(s)

Residential

Industry/Entity Type

Gardener

Font styles to use
Serif

Colors
9ccb3b
abd037
3176b5

Requirements
Must have
• my services, my logo, my contact details,

```html
<!DOCTYPE html>
<html lang="en">
<head>
<meta charset="utf-8">
<title>Marlowe Grove – DL Flyer</title>
<link rel="stylesheet" href="https://fonts.googleapis.com/css2?family=Oswald:wght@500;600&family=Lora:wght@400;700&display=swap">
<style>
  :root {
    --stage: #dcdcdc;
    --blue-light: #5db8e8;
    --blue-deep: #3176b5;
    --lawn: #9ccb3b;
    --lawn-bright: #abd037;
    --badge: #9ccb3b;
    --ink: #1f2a1a;
    --white: #ffffff;
  }
  * { box-sizing: border-box; margin: 0; padding: 0; }
  html, body {
    width: 1200px; height: 900px; overflow: hidden;
    background: var(--stage);
  }
  .flyer {
    position: absolute; left: 390px; top: 10px;
    width: 420px; height: 880px; overflow: hidden;
    background: linear-gradient(180deg, var(--blue-light) 40%, var(--blue-deep) 100%);
    color: var(--white);
    font-family: "Lora", Georgia, serif;
    box-shadow: 0 12px 30px rgba(0,0,0,.25);
  }
  .hero-photo { position: absolute; left: 0; top: 0; width: 420px; height: 480px; }
  .brand {
    position: absolute; left: 28px; top: 160px;
    display: flex; align-items: center; gap: 10px;
    font-size: 28px; font-weight: 400; color: var(--white);
  }
  .brand-dot { width: 16px; height: 16px; border-radius: 50%; background: var(--white); }
  .promises {
    position: absolute; left: 178px; top: 34px; list-style: none;
    font-family: "Oswald", "Arial Narrow", sans-serif; font-weight: 500;
    font-size: 17px; letter-spacing: .3px; line-height: 1.45;
    text-transform: uppercase;
  }
  .promises li { display: flex; align-items: center; gap: 8px; }
  .promises svg { width: 16px; height: 16px; flex: none; }
  .quote-badge { position: absolute; left: 258px; top: 262px; width: 150px; height: 150px; }
  .quote-badge text {
    font-family: "Oswald", "Arial Narrow", sans-serif; font-weight: 600;
    font-size: 22px; fill: var(--ink); text-anchor: middle;
  }
  .headline {
    position: absolute; left: 28px; top: 468px; width: 380px;
    font-family: "Oswald", "Arial Narrow", sans-serif; font-weight: 600;
    font-size: 30px; line-height: 1.1; text-transform: uppercase;
  }
  .intro {
    position: absolute; left: 28px; top: 542px; width: 370px;
    font-size: 12.5px; line-height: 1.35;
  }
  .services-title {
    position: absolute; left: 50%; top: 606px; transform: translateX(-50%);
    border: 3px solid var(--white); padding: 1px 22px;
    font-family: "Oswald", "Arial Narrow", sans-serif; font-weight: 500;
    font-size: 23px; text-transform: uppercase; white-space: nowrap;
  }
  .service-list {
    position: absolute; top: 658px; list-style: none;
    font-size: 12.5px; line-height: 1.3;
  }
  .service-list.main { left: 28px; }
  .service-list.extra { left: 262px; }
  .appointment {
    position: absolute; left: 0; right: 0; top: 772px; text-align: center;
    font-family: "Oswald", "Arial Narrow", sans-serif; font-weight: 600;
    font-size: 30px; line-height: 1.2; text-transform: uppercase;
  }
  .contact-band {
    position: absolute; left: 0; bottom: 0; width: 100%; height: 64px;
    background: linear-gradient(90deg, var(--lawn) 0%, var(--lawn-bright) 100%);
    color: var(--ink); padding: 12px 20px;
    font-size: 13px; font-weight: 700; line-height: 1.45; text-align: center;
  }
  .contact-band .divider { margin: 0 6px; }
</style>
</head>
<body>
  <main class="flyer">
    <svg class="hero-photo" role="img" aria-label="Photo of a white gabled family house with a freshly mown green lawn under a blue sky" viewBox="0 0 420 480">
      <defs>
        <linearGradient id="skyFade" x1="0" y1="0" x2="0" y2="1">
          <stop offset="0" stop-color="#3d9be0"/>
          <stop offset="0.45" stop-color="#7cc4ee"/>
          <stop offset="0.55" stop-color="#c9d9c4"/>
          <stop offset="0.7" stop-color="#9ccb3b"/>
          <stop offset="1" stop-color="#6f9a2c"/>
        </linearGradient>
      </defs>
      <polygon points="0,0 420,0 420,370 0,480" fill="url(#skyFade)"/>
    </svg>

    <div class="brand"><span class="brand-dot"></span>Marlowe Grove</div>

    <ul class="promises">
      <li><svg viewBox="0 0 16 16"><path d="M2 9 L6 13 L14 3" fill="none" stroke="#fff" stroke-width="3"/></svg>Reliable and friendly service</li>
      <li><svg viewBox="0 0 16 16"><path d="M2 9 L6 13 L14 3" fill="none" stroke="#fff" stroke-width="3"/></svg>12 years experience</li>
      <li><svg viewBox="0 0 16 16"><path d="M2 9 L6 13 L14 3" fill="none" stroke="#fff" stroke-width="3"/></svg>Great rates</li>
    </ul>

    <svg class="quote-badge" viewBox="0 0 160 160">
      <g fill="var(--badge)">
        <rect x="25" y="25" width="110" height="110"/>
        <rect x="25" y="25" width="110" height="110" transform="rotate(15 80 80)"/>
        <rect x="25" y="25" width="110" height="110" transform="rotate(30 80 80)"/>
        <rect x="25" y="25" width="110" height="110" transform="rotate(45 80 80)"/>
        <rect x="25" y="25" width="110" height="110" transform="rotate(60 80 80)"/>
        <rect x="25" y="25" width="110" height="110" transform="rotate(75 80 80)"/>
      </g>
      <text x="80" y="62">FREE NO</text>
      <text x="80" y="88">OBLIGATION</text>
      <text x="80" y="114">QUOTES</text>
    </svg>

    <h1 class="headline">A beautiful garden<br>doesn't happen by itself</h1>
    <p class="intro">Marlowe Grove is your garden and lawn care specialist, with a passion for gardening and a keen eye for detail you can rest assured you're in the right hands.</p>

    <h2 class="services-title">Our services</h2>

    <ul class="service-list main">
      <li>- pressure cleaning,</li>
      <li>- Eco Friendly fertilizing,</li>
      <li>- green waste removal,</li>
      <li>- tree and shrub pruning,</li>
      <li>- Full garden makeovers,</li>
      <li>- Timber deck rejuvenation,</li>
      <li>- Turf preparation and installation,</li>
    </ul>
    <ul class="service-list extra">
      <li>- lawn mowing,</li>
      <li>- weeding,</li>
      <li>- Mulching,</li>
      <li>- hedging,</li>
      <li>- privacy screening,</li>
      <li>- Planting,</li>
      <li>- and much more</li>
    </ul>

    <p class="appointment">Book an appointment</p>

    <footer class="contact-band">
      <p>Phone 0481527306<span class="divider">|</span>www.marlowegrove.com.au</p>
      <p>Email tom@marlowegrove.com.au</p>
    </footer>
  </main>
</body>
</html>
```